Modern Business Card for Larkwell 2018

Our company assumes the best about people. We are creating an online community of entrepreneurs and business leaders who struggle with marketing their business online.

This business card should POP! We recently got a new logo and are launching a new website next month, so our business cards should make a statement that feels:
-Fresh
-Smart
-Trustworthy
-Fun

Target Market(s)

small business owners, entrepreneurs

Industry/Entity Type

Digital Marketing

Contact Information for Business Card

Dimensions: 3.5" x 2"

Font styles to use
Sans Serif

Colors
f37122
ffffff

Requirements
Must have
• We need a business card with a modern, bold design. We will use one side of the card as a lead-generation offer, so text on one side will need to fit up to 140 characters. The business card should stick to our core colors (orange, black, and white).
Nice to have
• We think a vertical "portrait" design could be interesting.
Should not have
• Should not look like a traditional business card. The round icon should stand out from a distance.

```html
<!DOCTYPE html>
<html lang="en">
<head>
<meta charset="utf-8">
<title>Larkwell Business Card</title>
<link href="https://fonts.googleapis.com/css2?family=Barlow:wght@500;600;700&family=Barlow+Semi+Condensed:wght@600;700&family=Permanent+Marker&family=Merriweather:ital,wght@1,700&display=swap" rel="stylesheet">
<style>
  :root {
    --orange: #f37122;
    --white: #ffffff;
    --charcoal: #323132;
    --ink: #2b2b2b;
    --backdrop: #e4e4e4;
  }
  html, body {
    margin: 0;
    width: 1200px;
    height: 1200px;
    overflow: hidden;
    background: var(--backdrop);
    font-family: "Barlow", Arial, sans-serif;
  }
  .card {
    position: absolute;
    left: 219px;
    width: 762px;
    height: 435px;
    overflow: hidden;
    box-shadow: 0 18px 30px rgba(0,0,0,0.18);
  }
  .card--front { top: 105px; background: var(--white); }
  .card--back { top: 627px; background: var(--orange); }

  /* Front */
  .front__mark {
    position: absolute;
    left: 50%;
    top: 30px;
    transform: translateX(-50%);
    width: 150px;
    height: 150px;
    border-radius: 50%;
    background: var(--orange);
  }
  .front__brand {
    position: absolute;
    top: 192px;
    width: 100%;
    text-align: center;
    font-weight: 700;
    font-size: 40px;
    color: var(--orange);
    letter-spacing: 1px;
  }
  .front__role {
    position: absolute;
    top: 272px;
    width: 100%;
    text-align: center;
    font-weight: 500;
    font-size: 22px;
    color: var(--ink);
  }
  .front__band {
    position: absolute;
    left: 0;
    bottom: 0;
    width: 100%;
    height: 131px;
    background: var(--charcoal);
    color: var(--white);
    text-align: center;
  }
  .front__name {
    margin: 10px 0 0;
    font-family: "Permanent Marker", "Brush Script MT", cursive;
    font-size: 46px;
    font-weight: 400;
    line-height: 64px;
    letter-spacing: 1px;
  }
  .front__email {
    margin: 0;
    font-size: 28px;
    font-weight: 500;
    letter-spacing: 0.5px;
  }

  /* Back */
  .back__identity {
    position: absolute;
    left: 30px;
    top: 68px;
    width: 366px;
    text-align: center;
    color: var(--white);
  }
  .back__dot {
    display: block;
    margin: 0 auto 8px;
    width: 68px;
    height: 68px;
    border-radius: 50%;
    background: var(--white);
  }
  .back__brand {
    margin: 0;
    font-weight: 700;
    font-size: 62px;
    line-height: 64px;
    letter-spacing: 1px;
  }
  .back__tagline {
    margin: 2px 0 0;
    font-family: "Merriweather", Georgia, serif;
    font-style: italic;
    font-weight: 700;
    font-size: 19px;
  }
  .benefits {
    position: absolute;
    left: 427px;
    top: 118px;
    margin: 0;
    padding: 0;
    list-style: none;
  }
  .benefits__item {
    width: 335px;
    height: 43px;
    margin-bottom: 12px;
    background: var(--white);
    border-radius: 22px 0 0 22px;
    font-family: "Barlow Semi Condensed", Arial, sans-serif;
    font-weight: 700;
    font-size: 27px;
    line-height: 43px;
    text-align: center;
    color: var(--ink);
    letter-spacing: 0.3px;
  }
  .offer {
    position: absolute;
    left: 0;
    bottom: 0;
    width: 100%;
    height: 103px;
    background: var(--charcoal);
    color: var(--white);
    text-align: center;
  }
  .offer__lead {
    margin: 14px 0 0;
    font-size: 20px;
    font-weight: 500;
  }
  .offer__url {
    margin: 2px 0 0;
    font-size: 32px;
    font-weight: 600;
    letter-spacing: 1px;
  }
</style>
</head>
<body>
  <section class="card card--front">
    <span class="front__mark"></span>
    <div class="front__brand">Larkwell</div>
    <div class="front__role">Story Marketing Coach</div>
    <div class="front__band">
      <h1 class="front__name">DANA WHITCOMBE</h1>
      <p class="front__email">dana@larkwellnow.com</p>
    </div>
  </section>

  <section class="card card--back">
    <div class="back__identity">
      <span class="back__dot"></span>
      <h2 class="back__brand">LARKWELL</h2>
      <p class="back__tagline">Tell Stories That Inspire Action</p>
    </div>
    <ul class="benefits">
      <li class="benefits__item">REACH MORE PEOPLE</li>
      <li class="benefits__item">MAKE MORE MONEY</li>
      <li class="benefits__item">CREATE MORE IMPACT</li>
    </ul>
    <div class="offer">
      <p class="offer__lead">Get your free Larkwell Starter Package and our marketing guide today at</p>
      <p class="offer__url">larkwellnow.com/start</p>
    </div>
  </section>
</body>
</html>
```